Webshop Template

For our Webstore in UK we need a complete Template,
shoppingcart is Magento, the Shop is focussed on Download software,

the name: Kelvoramarket.co.uk

Check out some other good stores, like zandrilo.de
Updates

for example the Page from 

www.brunt.co.uk or

www.zandrilo.de

www.mokvelta.de

www.quarnepreis.de

The Logodesign which are in Consideration

http://www.plimvector.com/design/5520913/logo-design-by-tomek7ga

http://www.plimvector.com/design/5518207/logo-design-by-ivanoralba

http://www.plimvector.com/design/5517346/logo-design-by-granite-fables

http://www.plimvector.com/design/5516085/logo-design-by-quillotaste

http://www.plimvector.com/design/5515472/logo-design-by-tuvaro

http://www.plimvector.com/design/5514619/logo-design-by-lone-pine-graphic-

Target Market(s)

B2C - Consumer Marcet

Industry/Entity Type

Shop

```html
<!DOCTYPE html>
<html lang="en">
<head>
<meta charset="utf-8">
<title>Kelvoramarket.co.uk — Download Software Store</title>
<link rel="stylesheet" href="https://fonts.googleapis.com/css2?family=Open+Sans:wght@400;600;700&family=PT+Sans:wght@400;700&display=swap">
<style>
:root{
  --red:#d40000;
  --ink:#222;
  --text:#444;
  --line:#dcdcdc;
  --panel:#f4f4f4;
  --dark:#1c1c1c;
  --white:#fff;
}
*{box-sizing:border-box;margin:0;padding:0}
html,body{width:1187px;height:1200px;overflow:hidden}
body{position:relative;background:var(--white);font-family:"Open Sans",sans-serif;color:var(--text);font-size:12px}
a{color:inherit;text-decoration:none}
.abs{position:absolute}

.header-band{left:0;top:0;width:1187px;height:144px;background:linear-gradient(#fbfbfb,#ececec);border-bottom:1px solid #d6d6d6}
.footer-band{left:0;top:849px;width:1187px;height:351px;background:var(--panel)}

.brand{left:114px;top:22px;display:flex;align-items:center;gap:12px}
.brand-mark{width:56px;height:56px;background:#444;border:3px solid #222}
.brand-name{font-family:"PT Sans",sans-serif;font-size:21px;color:#333;letter-spacing:.3px}

.welcome{left:422px;top:20px;font-size:12px;color:#333}
.welcome a{text-decoration:underline}
.search{left:418px;top:66px;width:351px;height:32px;display:flex;border:1px solid #ccc;background:#fff}
.search-field{flex:1;padding:6px 9px;color:#bbb;font-size:13px}
.search-btn{flex:none;width:41px;background:#222;display:flex;align-items:center;justify-content:center}
.account{right:246px;top:20px;display:flex;gap:15px;color:#333}
.cart{left:950px;top:9px;width:118px;height:34px;background:var(--dark);border-radius:3px;display:flex;align-items:center;color:#fff;font-weight:600}
.cart svg{margin:0 12px 0 10px;flex:none}
.cart b{border-left:1px solid #555;padding-left:10px;font-weight:600;white-space:nowrap}
.promo{right:117px;top:72px;display:flex;gap:10px;color:#666;font-size:12px}
.phone{right:117px;top:90px;color:#666}

.nav{left:117px;top:123px;width:947px;height:39px;background:linear-gradient(#e00d0d,#b80000);border-radius:3px;display:flex;justify-content:space-between;align-items:center;padding:0 17px 0 20px;box-shadow:0 2px 2px rgba(0,0,0,.2)}
.nav a{font-family:"PT Sans",sans-serif;font-weight:700;font-size:15px;color:#fff}

.hero{left:116px;top:180px;width:953px;height:301px;border:1px solid var(--line);border-radius:4px;background:linear-gradient(90deg,#f6f6f6,#fff 60%,#f0f0f0);overflow:hidden}
.hero-menu{position:absolute;left:0;top:0;width:174px;height:100%}
.hero-menu li{list-style:none;height:75px;padding:15px 18px;background:linear-gradient(#f0f0f0,#e2e2e2);border-bottom:1px solid #fff}
.hero-menu h4{font-family:"PT Sans",sans-serif;font-weight:400;font-size:14px;color:#222}
.hero-menu p{font-size:11px;color:#999;line-height:14px;margin-top:4px}
.hero-title{position:absolute;left:199px;top:30px;font-family:"PT Sans",sans-serif;font-weight:700;font-size:31px;line-height:40px;color:#222}
.hero-copy{position:absolute;left:196px;top:129px;width:370px;font-size:12px;line-height:18px;color:#666}
.shop-now{position:absolute;left:197px;top:205px;width:110px;height:35px;background:var(--dark);color:#fff;font-family:"PT Sans",sans-serif;font-weight:700;font-size:14px;display:flex;align-items:center;padding-left:11px;border-radius:2px}
.hero-price{position:absolute;left:320px;top:209px;font-family:"PT Sans",sans-serif;font-size:23px;color:var(--red)}
.dots{position:absolute;left:210px;top:280px;display:flex;gap:3px}
.dots i{width:6px;height:6px;border:1px solid #ccc;background:#fff}
.dots i.on{background:#222;border-color:#222}
.hero-art{position:absolute;left:693px;top:22px;width:222px;height:258px;background:linear-gradient(135deg,#c3121a,#7a0a0f)}

.section-bar{left:116px;top:500px;width:948px;height:40px;background:linear-gradient(#333,#151515);border-radius:3px;color:#fff;font-family:"PT Sans",sans-serif;font-weight:700;font-size:15px;padding:11px 13px}
.bar-arrows{position:absolute;right:0;top:0;display:flex;height:40px}
.bar-arrows span{width:39px;border-left:1px solid #444;display:flex;align-items:center;justify-content:center}

.products{left:130px;top:583px;width:920px;display:flex;justify-content:space-between}
.product{width:120px}
.product-art{width:100px;height:130px;margin-bottom:30px}
.product h5{font-weight:400;font-size:12.5px;color:#222}
.product p{font-size:13px;color:#666;margin-top:2px}
.product p b{font-family:"PT Sans",sans-serif;font-weight:400;font-size:15px;color:var(--red)}

.partners{left:110px;top:808px;width:967px;height:90px;background:#fff;border:1px solid #e2e2e2;display:flex;align-items:center;justify-content:space-around;padding:0 28px}
.partners i{display:block;background:#d9d9d9;height:40px;border-radius:3px}
.partners .chev{position:absolute;top:36px;color:#ccc;font-size:18px}

.foot-col{top:942px}
.foot-col h6{font-weight:600;font-size:12.5px;color:#222;margin-bottom:20px;letter-spacing:.2px}
.foot-col li{list-style:none;font-size:11.5px;color:#555;height:22px}
.social li{height:31px;display:flex;align-items:center;gap:12px;padding-left:2px}
.social i{width:20px;height:20px;border-radius:3px}
.newsletter{left:729px;top:938px;width:352px;height:100px;background:var(--red);border-radius:3px;overflow:hidden}
.newsletter h6{background:#000;color:#fff;font-weight:700;font-size:11.5px;padding:8px 10px;height:30px}
.newsletter p{color:#fff;font-size:11px;padding:6px 9px}
.nl-form{display:flex;gap:8px;padding:0 10px}
.nl-field{width:249px;height:25px;background:#fff;border:1px solid #ddd;font-size:11px;color:#666;padding:4px 13px}
.nl-btn{width:74px;height:25px;background:linear-gradient(#fafafa,#ddd);font-size:11.5px;color:#333;display:flex;align-items:center;justify-content:center}
.help{left:729px;top:1056px;font-size:10px;font-weight:700;color:#222;text-decoration:underline}
.help-phone{left:729px;top:1070px;font-family:"PT Sans",sans-serif;font-weight:700;font-size:20px;color:#111}
.foot-rule{left:117px;top:1127px;width:963px;height:1px;background:var(--line)}
.copyright{left:111px;top:1170px;font-size:11px;color:#444}
.payments{left:686px;top:1150px;display:flex;gap:9px}
.payments span{width:56px;height:32px;background:#fff;border:1px solid #ddd;border-radius:3px;font-size:9.5px;font-weight:700;color:#1a3b8c;display:flex;align-items:center;justify-content:center;white-space:nowrap}
</style>
</head>
<body>
<div class="abs header-band"></div>
<div class="abs footer-band"></div>

<header>
  <a class="abs brand" href="#"><span class="brand-mark"></span><span class="brand-name">Kelvoramarket.co.uk</span></a>
  <p class="abs welcome">Welcome to our online store! <a href="#">Sign In</a> or <a href="#">Sign Up</a></p>
  <div class="abs search"><span class="search-field">Search</span><span class="search-btn"><svg width="20" height="20" viewBox="0 0 20 20"><circle cx="8" cy="8" r="6" fill="none" stroke="#fff" stroke-width="2.5"/><line x1="12.5" y1="12.5" x2="18" y2="18" stroke="#fff" stroke-width="3"/></svg></span></div>
  <nav class="abs account"><a href="#">My Account</a><a href="#">My wishlist</a><a href="#">Checkout</a></nav>
  <div class="abs cart"><svg width="20" height="18" viewBox="0 0 20 18"><path d="M1 2h3l3 9h9l2-6H6" fill="none" stroke="#fff" stroke-width="2"/><circle cx="8" cy="15" r="1.6" fill="#fff"/><circle cx="15" cy="15" r="1.6" fill="#fff"/></svg><b>0 items (s)</b></div>
  <nav class="abs promo"><a href="#">OVERSTOCK DEALS</a><a href="#">FREE SHIPPING</a><a href="#">GIFT CARD</a></nav>
  <p class="abs phone">010-XXX-XXX-XXX</p>
  <nav class="abs nav"><a href="#">HOME</a><a href="#">SOFTWARE</a><a href="#">NOVA GAMES</a><a href="#">WAVE GAMES</a><a href="#">ZENBOX GAMES</a><a href="#">DUO GAMES</a><a href="#">PC GAMES</a></nav>
</header>

<section class="abs hero">
  <ul class="hero-menu">
    <li><h4>EMAILS SOFTWARE</h4><p>Lorem Ipsum is simply dummy</p></li>
    <li><h4>DEAL OF THE DAY</h4><p>Lorem Ipsum is simply dummy</p></li>
    <li><h4>SAVE OF &nbsp;20%</h4><p>Lorem Ipsum is simply dummy</p></li>
    <li><h4>POPULAT SOFTWARE</h4><p>Lorem Ipsum is simply dummy</p></li>
  </ul>
  <h1 class="hero-title">Download your 2013 Free 3D<br>Software</h1>
  <p class="hero-copy">Lorem Ipsum is simply dummy text of the printing and typesetting industry. Lorem Ipsum has been the industry's standard dummy text ever since the 1500s,</p>
  <a class="shop-now" href="#">SHOP NOW &nbsp;›</a>
  <p class="hero-price">$1200.00</p>
  <div class="dots"><i></i><i class="on"></i><i></i><i></i></div>
  <div class="hero-art" role="img" aria-label="Two red software boxes of a design suite"></div>
</section>

<div class="abs section-bar">NEW SOFTWARES
  <div class="bar-arrows"><span><svg width="10" height="14"><path d="M8 1L2 7l6 6" fill="none" stroke="#fff" stroke-width="2.5"/></svg></span><span><svg width="10" height="14"><path d="M2 1l6 6-6 6" fill="none" stroke="#fff" stroke-width="2.5"/></svg></span></div>
</div>

<section class="abs products">
  <article class="product"><div class="product-art" role="img" aria-label="Blue and white software box" style="background:linear-gradient(135deg,#e8f4fb,#1a7dc0)"></div><h5>Zenbox software</h5><p>From <b>$10.00</b></p></article>
  <article class="product"><div class="product-art" role="img" aria-label="Black audio software box" style="background:linear-gradient(135deg,#3a3f46,#111)"></div><h5>Nova software</h5><p>From <b>$10.00</b></p></article>
  <article class="product"><div class="product-art" role="img" aria-label="White software box with orange graphic" style="background:linear-gradient(160deg,#eef1f8,#f39a1e)"></div><h5>Wave Games</h5><p>From <b>$10.00</b></p></article>
  <article class="product"><div class="product-art" role="img" aria-label="Red disc burning software box" style="background:linear-gradient(135deg,#d8262b,#8e1014)"></div><h5>Duo Games</h5><p>From <b>$10.00</b></p></article>
  <article class="product"><div class="product-art" role="img" aria-label="Silver security software box" style="background:linear-gradient(135deg,#f2f4f8,#8b9bb6)"></div><h5>Vantor Software</h5><p>From <b>$10.00</b></p></article>
</section>

<section class="abs partners" aria-label="Registered partners">
  <span class="chev" style="left:10px">‹</span>
  <i style="width:104px"></i><i style="width:112px"></i><i style="width:142px"></i><i style="width:150px"></i><i style="width:112px"></i><i style="width:118px"></i>
  <span class="chev" style="right:8px">›</span>
</section>

<footer>
  <div class="abs foot-col" style="left:114px"><h6>SOFTWARE</h6><ul><li>Picturo</li><li>Zemba</li><li>Lorem Lipsum</li><li>Short Cruises</li><li>Cruise Calendar</li></ul></div>
  <div class="abs foot-col" style="left:313px"><h6>GET INFO</h6><ul><li>My Cruises</li><li>Countdown to Cruise</li><li>Online Check-in</li><li>Pre-cruise Planner</li><li>Shore &amp; Land Excursions</li></ul></div>
  <div class="abs foot-col social" style="left:513px"><h6>SHARE &amp; CONNECT</h6><ul>
    <li><i style="background:#3b5998"></i>Friendloop</li>
    <li><i style="background:#5bc0de"></i>Chirplane</li>
    <li><i style="background:#3b6fc9"></i>Goventa</li>
    <li><i style="background:#f2891b"></i>RSS</li></ul></div>
  <div class="abs newsletter"><h6>SIGN UP FOR OUR NEWSLETTER</h6><p>Sign up to recieve special offers and deals</p><div class="nl-form"><span class="nl-field">Enter your email address</span><span class="nl-btn">Subscribe</span></div></div>
  <p class="abs help">NEED HELP? WE'RE AVAILABLE AT</p>
  <p class="abs help-phone">0100-xxxx xxx</p>
  <div class="abs foot-rule"></div>
  <p class="abs copyright">Kelvoramarket © 2013 | Privacy Policy | Terms Of Use</p>
  <div class="abs payments"><span>Vendcheck</span><span>Marlocard</span><span>Versafe</span><span>Vexa</span><span>Marlocard</span><span>Paywell</span></div>
</footer>
</body>
</html>
```